NZ First of it's kind solutions directory and marketplace for busy Mums needs a business card design

We need a business card design for our new nationwide business in NZ (long term plans to go global). We provide solutions to the everyday challenges that busy Mums face by connecting them with quality communities and suppliers of carefully selected, relevant products and services. We sell direct via our online marketplace. The final design should communicate our values of inclusivity, quality and smart solutions. Colours should incorporate our logo colour palette of #477077 and #6ba8b2. Our website is at https://www.brightnestmums.example

Target Market(s)

busy Mums, Age 28 – 50, female, income over $100K, location main centres NZ primarily but NZ wide. Is likely juggling work or career with a young family. Probably had hobbies which have fallen by the wayside.
-Wants to succeed in her chosen career without compromising on family life
-to successfully juggle her career without feeling like she is compromising her children
- Is time poor, something always has to give and it’s generally her health (she’ll stay up late, get stressed)
- probably ex corporate or professional career. Has discretional income

Industry/Entity Type

Business

Contact Information for Business Card

Lena Forbisher, Founder, BrightNestMums.example (Strapline Tap; Gather; Sorted), 47 Kowhai Terrace, Ellerslie, Auckland 1051, New Zealand. Mob: 021 483 517 Ph: +64 (0)9 571 4860

Font styles to use
Other font styles liked:
• Raleway, and/or Architects Daughter

Colors
00a990
33b8a4
86cfc6
cfeae6

Requirements
Must have
• the above details, streamline. the logo and colours associated with those logos
Should not have
• foil or metallic colours

```html
<!DOCTYPE html>
<html lang="en">
<head>
<meta charset="utf-8">
<title>BrightNest Mums – Business Card</title>
<link rel="stylesheet" href="https://fonts.googleapis.com/css2?family=Fredoka:wght@600&family=Roboto:ital,wght@0,400;1,400&display=swap">
<style>
  :root {
    --teal-dark: #3d5f66;
    --teal-mid: #477077;
    --teal-light: #6ba8b2;
    --paper: #f6f6f6;
    --stage: #e6e6e6;
    --ink: #3a3a3a;
    --ink-soft: #555;
    --white: #ffffff;
  }
  * { margin: 0; padding: 0; box-sizing: border-box; }
  html, body { width: 1200px; height: 576px; overflow: hidden; }
  body {
    position: relative;
    background: var(--stage);
    font-family: "Roboto", Arial, sans-serif;
  }
  .card {
    position: absolute;
    top: 138px;
    width: 484px;
    height: 293px;
    border-radius: 14px;
    overflow: hidden;
    box-shadow: 0 3px 8px rgba(0,0,0,0.18);
  }
  .card--front { left: 82px; background: var(--teal-dark); }
  .card--back { left: 602px; width: 481px; height: 292px; background: var(--paper); }

  .brand-name {
    font-family: "Fredoka", "Trebuchet MS", sans-serif;
    font-weight: 600;
    white-space: nowrap;
    line-height: 1;
  }
  .strapline {
    text-transform: uppercase;
    white-space: nowrap;
    line-height: 1;
  }

  .front-lockup {
    position: absolute;
    left: 0; right: 0; top: 114px;
    text-align: center;
  }
  .front-lockup .brand-name { font-size: 45px; color: var(--white); }
  .front-lockup .strapline {
    margin-top: 18px;
    font-size: 14px;
    letter-spacing: 4.6px;
    color: var(--white);
  }

  .back-lockup {
    position: absolute;
    left: 22px; width: 220px; top: 96px;
    text-align: center;
  }
  .brand-dot {
    display: block;
    width: 44px; height: 44px;
    margin: 0 auto 24px;
    border-radius: 50%;
    background: var(--teal-mid);
  }
  .back-lockup .brand-name { font-size: 26px; color: var(--teal-mid); }
  .back-lockup .strapline {
    margin-top: 9px;
    font-size: 9px;
    letter-spacing: 2.8px;
    color: var(--ink);
  }

  .contact {
    position: absolute;
    left: 268px; top: 52px;
    color: var(--ink);
  }
  .contact__name {
    font-family: "Fredoka", "Trebuchet MS", sans-serif;
    font-weight: 600;
    font-size: 20px;
    color: var(--teal-mid);
    line-height: 1;
  }
  .contact__role {
    margin-top: 5px;
    font-style: italic;
    font-size: 12px;
    color: var(--ink-soft);
  }
  .contact__address {
    margin-top: 17px;
    font-size: 12.5px;
    line-height: 18px;
    font-style: normal;
  }
  .contact__list { margin-top: 11px; list-style: none; }
  .contact__list li {
    display: flex; align-items: center;
    font-size: 12.5px; height: 18.5px;
  }
  .contact__list svg { width: 11px; height: 11px; margin-right: 8px; fill: var(--teal-mid); }

  .band-strip {
    position: absolute; left: 0; bottom: 0;
    width: 240px; height: 11px;
    background: var(--teal-light);
  }
  .band {
    position: absolute; right: 0; bottom: 0;
    width: 262px; height: 36px;
    background: var(--teal-dark);
    clip-path: polygon(18px 0, 100% 0, 100% 100%, 0 100%);
  }
  .band__url {
    position: absolute; left: 268px; bottom: 11px;
    font-size: 12px; color: var(--white);
  }
</style>
</head>
<body>
  <section class="card card--front" aria-label="Card front">
    <div class="front-lockup">
      <div class="brand-name">BrightNest Mums</div>
      <div class="strapline">Tap &nbsp;|&nbsp; Gather &nbsp;|&nbsp; Sorted</div>
    </div>
  </section>

  <section class="card card--back" aria-label="Card back">
    <div class="back-lockup">
      <span class="brand-dot"></span>
      <div class="brand-name">BrightNest Mums</div>
      <div class="strapline">Tap | Gather | Sorted</div>
    </div>

    <div class="contact">
      <div class="contact__name">Lena Forbisher</div>
      <div class="contact__role">Founder</div>
      <address class="contact__address">47 Kowhai Terrace, Ellerslie,<br>Auckland 1051, New Zealand</address>
      <ul class="contact__list">
        <li><svg viewBox="0 0 12 12" aria-hidden="true"><path d="M3 0h6a1 1 0 0 1 1 1v10a1 1 0 0 1-1 1H3a1 1 0 0 1-1-1V1a1 1 0 0 1 1-1zm0 1.5v7.5h6V1.5zM6 9.6a.8.8 0 1 0 0 1.6.8.8 0 0 0 0-1.6z"/></svg>021 483 517</li>
        <li><svg viewBox="0 0 12 12" aria-hidden="true"><path d="M1 3.5C1 2 3 1.5 6 1.5S11 2 11 3.5V5H8.5V3.8h-5V5H1zM3 6l1.2-1.5h3.6L9 6l1.5 4.5h-9zM6 6.8a1.3 1.3 0 1 0 0 2.6 1.3 1.3 0 0 0 0-2.6z"/></svg>+64 (0)9 571 4860</li>
        <li><svg viewBox="0 0 12 12" aria-hidden="true"><path d="M0 2h12v8H0zm1.2 1.2v.2L6 6.6l4.8-3.2v-.2zm0 1.6v4h9.6v-4L6 8z"/></svg>lena@brightnestmums.example</li>
      </ul>
    </div>

    <div class="band-strip"></div>
    <div class="band"></div>
    <div class="band__url">www.BrightNestMums.example</div>
  </section>
</body>
</html>
```